MEDICAL CLINIC LETTERHEAD

Design is a letterhead for a non-profit medical center. The name of the clinic is VITARIDGE Community Health Center. Although the full name must be included, the community health center part is more of a description and should be less visible - i attached an example of what I mean by that (ATTACHED IMAGE IS AN EXAMPLE OF FONT SIZES NOT A DESIGN IDEA). Please design something modern, cool looking and unique because I can always download free templates.
Phone, email, website and etc will be added later.

Industry/Entity Type

MEDICAL

```html
<!DOCTYPE html>
<html lang="en">
<head>
<meta charset="utf-8">
<title>VITARIDGE Community Health Center – Letterhead</title>
<link href="https://fonts.googleapis.com/css2?family=Didact+Gothic&family=Montserrat:wght@600&family=Open+Sans:wght@600&family=Questrial&display=swap" rel="stylesheet">
<style>
  :root {
    --navy: #16264d;
    --gold: #a78a56;
    --text-grey: #8c8c8f;
    --name-grey: #939396;
    --date-grey: #7f7f82;
    --paper: #ffffff;
  }
  * { margin: 0; padding: 0; box-sizing: border-box; }
  html, body { width: 908px; height: 1200px; overflow: hidden; background: var(--paper); }
  .letterhead {
    position: relative; width: 908px; height: 1200px; background: var(--paper);
    font-family: "Didact Gothic", "Questrial", sans-serif; color: var(--text-grey);
  }
  .brand { position: absolute; left: 27px; top: 44px; color: var(--navy); font-family: "Montserrat", sans-serif; font-weight: 600; }
  .brand__name { font-size: 30px; letter-spacing: -0.5px; line-height: 30px; }
  .brand__descriptor { font-size: 6px; letter-spacing: 0.3px; text-transform: uppercase; margin-top: 2px; }
  .header-rule { position: absolute; left: 0; top: 100px; width: 704px; height: 1.5px; background: var(--gold); }
  .contact { position: absolute; left: 709px; top: 46px; list-style: none; font-size: 13.5px; }
  .contact li { display: flex; align-items: center; height: 22.5px; }
  .contact svg { width: 11px; height: 11px; margin-right: 5px; flex: none; }
  .recipient { position: absolute; left: 41px; top: 234px; }
  .recipient__name { font-family: "Montserrat", sans-serif; font-weight: 600; font-size: 27px; color: var(--name-grey); letter-spacing: 0.3px; line-height: 34px; margin-bottom: 2px; }
  .recipient p { font-family: "Questrial", sans-serif; font-size: 15.5px; letter-spacing: 0.3px; line-height: 27px; color: var(--text-grey); }
  .recipient .address { line-height: 21px; margin-top: 3px; }
  .date { position: absolute; right: 43px; top: 350px; font-family: "Open Sans", sans-serif; font-weight: 600; font-size: 16.5px; color: var(--date-grey); }
  .body-copy { position: absolute; left: 36px; width: 829px; font-size: 16px; letter-spacing: 0.75px; line-height: 19.7px; text-align: justify; }
  .body-copy--one { top: 406px; }
  .body-copy--two { top: 544px; }
  .body-copy--three { top: 682px; }
  .signoff { position: absolute; left: 615px; top: 797px; font-size: 22.5px; color: var(--text-grey); }
  .signature { position: absolute; left: 634px; top: 852px; width: 168px; height: 98px; background: linear-gradient(135deg, #f3f3f4, #e8e8ea); border-radius: 4px; }
  .footer-band { position: absolute; left: 0; bottom: 0; width: 908px; height: 150px; display: block; }
</style>
</head>
<body>
<main class="letterhead">
  <header>
    <div class="brand">
      <div class="brand__name">VITARIDGE</div>
      <div class="brand__descriptor">Community Health Center</div>
    </div>
    <div class="header-rule"></div>
    <ul class="contact">
      <li><svg viewBox="0 0 12 12"><circle cx="6" cy="6" r="6" fill="var(--navy)"/><path d="M4 3.2l1 1.3-.6.7c.4.9 1 1.5 1.9 1.9l.7-.6 1.3 1-.6.9C5.6 8.3 3.7 6.4 3.1 3.8z" fill="#fff"/></svg>0123-555-014</li>
      <li><svg viewBox="0 0 12 12"><circle cx="6" cy="6" r="6" fill="var(--navy)"/><rect x="3" y="4" width="6" height="4.2" fill="#fff"/><path d="M3 4l3 2.3L9 4" stroke="var(--navy)" stroke-width=".8" fill="none"/></svg>info@vitaridge.com</li>
      <li><svg viewBox="0 0 12 12"><circle cx="6" cy="6" r="6" fill="var(--navy)"/><g stroke="#fff" stroke-width=".7" fill="none"><circle cx="6" cy="6" r="3.4"/><ellipse cx="6" cy="6" rx="1.4" ry="3.4"/><path d="M2.6 6h6.8"/></g></svg>www.vitaridge.com</li>
    </ul>
  </header>

  <section class="recipient">
    <h1 class="recipient__name">MARA ELLISON</h1>
    <p>0123-555-014</p>
    <p>hello@northlanepartners.com</p>
    <p class="address">4810 Alder Grove Ln. Suite<br>210 Denton, TX 0000</p>
  </section>
  <div class="date">12 December, 2023</div>

  <p class="body-copy body-copy--one">Lorem ipsum dolor sit amet, consectetuer adipiscing elit, sed diam nonummy nibh euismod tincidunt ut laoreet dolore magna aliquam erat volutpat. Ut wisi enim ad minim veniam, quis nostrud exerci tation ulla­mcorper suscipit lobortis nisl ut aliquip ex ea commodo consequat. Duis autem vel eum iriure dolor in hen­drerit in vulputate velit esse molestie consequat, vel illum dolore eu feugiat nulla facilisis at vero eros et accumsan et iusto odio dignissim qui blandit praesent luptatum zzril delenit augue duis dolore te feugait nulla facilisi.</p>
  <p class="body-copy body-copy--two">Lorem ipsum dolor sit amet, cons ectetuer adipiscing elit, sed diam nonummy nibh euismod tincidunt ut laoreet dolore magna aliquam erat volutpat. Ut wisi enim ad minim veniam, quis nostrud exerci tation ulla­mcorper suscipit lobortis nisl ut aliquip ex ea commodo consequat.<br>Lorem ipsum dolor sit amet, consectetuer adipiscing elit, sed diam nonummy nibh euismod tincidunt ut laoreet dolore magna aliquam erat</p>
  <p class="body-copy body-copy--three">Lorem ipsum dolor sit amet, cons ectetuer adipiscing elit, sed diam nonummy nibh euismod tincidunt ut laoreet dolore magna aliquam erat volutpat. Ut wisi enim ad minim veniam, quis nostrud exerci tation ulla­mcorper suscipit lobortis nisl ut aliquip ex ea commodo consequat. Lorem ipsum dolor sit zamet, consec­tetuer adipiscing elit, sed diam nonummy nibh euismod tincidunt.</p>

  <div class="signoff">Managing Director</div>
  <div class="signature" role="img" aria-label="Handwritten signature of the managing director"></div>

  <svg class="footer-band" viewBox="0 0 908 150" preserveAspectRatio="none" aria-hidden="true">
    <path d="M0 96 Q454 30 908 70" stroke="var(--gold)" stroke-width="7" fill="none"/>
    <path d="M0 112 Q454 46 908 86 L908 150 L0 150 Z" fill="var(--navy)"/>
  </svg>
</main>
</body>
</html>
```